Design and Renovation Company Luxury Business Card

I want to create a luxury business card for a Design and Renovation Firm . We will use our current logo. The company name is 528BUILDA. We do not want anything standard. We need a very unique concept.
Please see uploaded inspiration. I really like the textured paper option. I would like the card to be thick with debossing, and/or embossing options. The logo has orange in it but I would like to see the card with and without the orange. I think the orange may make the company feel less high-end. The goal is to elevate the logo not match its vibe per se of the logo. We want something very unique, not standard at all!
I would like a space for :
Logo,
Name,
Position,
Email,
Office number,
Website Address,
Business Address,
Thank you!
Have fun!
Target Market(s)
Home owners Age 35 +
Industry/Entity Type
Design and Renovation
Contact Information for Business Card
Logo, Name, Position, Email, Office number, Website Address, Business Address,.
Colors
Designer to choose colors to be used in the design.
Requirements
Must have
- A luxury designer feel. Must be black or dark grey but open to other luxury ideas.
Nice to have
- Gold, silver, black embossing or debossing. Textured paper design.
Should not have
- A cheap look and feel.

```html
<!DOCTYPE html>
<html lang="en">
<head>
<meta charset="utf-8">
<title>528BUILDA Business Card</title>
<link href="https://fonts.googleapis.com/css2?family=Montserrat:wght@400;700&display=swap" rel="stylesheet">
<style>
  :root {
    --backdrop: #6b6b6b;
    --card-black: #181818;
    --brand-orange: #f7941e;
    --white: #ffffff;
    --deboss-olive: #6e5f26;
  }
  * { margin: 0; padding: 0; box-sizing: border-box; }
  html, body {
    width: 1200px; height: 801px; overflow: hidden;
    background: var(--backdrop);
    font-family: "Montserrat", sans-serif;
  }
  .canvas {
    position: relative; width: 1200px; height: 801px;
    display: flex; align-items: center; justify-content: center; gap: 40px;
  }
  .card {
    position: relative; width: 540px; height: 309px;
    box-shadow: 0 14px 30px rgba(0,0,0,0.35);
  }

  /* Front: contact side */
  .card--front {
    background: var(--card-black);
    border-bottom: 2px solid var(--brand-orange);
    display: flex; align-items: center;
  }
  .company {
    width: 285px; padding-left: 44px;
    color: var(--white); font-weight: 400; font-size: 30px;
    letter-spacing: 1px; line-height: 1; white-space: nowrap;
  }
  .divider {
    width: 1.5px; height: 190px; background: var(--brand-orange);
    margin-right: 26px; flex: none;
  }
  .contact { color: var(--white); font-size: 12.5px; line-height: 1.55; }
  .contact__name {
    color: var(--brand-orange); font-weight: 700; font-size: 21px;
    letter-spacing: 0.5px; line-height: 1.2;
  }
  .contact__role { margin-bottom: 6px; }
  .contact__item { display: flex; align-items: center; gap: 7px; }
  .contact__icon { width: 12px; height: 12px; flex: none; }

  /* Back: name side */
  .card--back {
    background: var(--brand-orange);
    display: flex; align-items: center; justify-content: center;
  }
  .company--back {
    width: auto; padding: 0;
    color: var(--deboss-olive); font-size: 58px; letter-spacing: 2px;
  }
</style>
</head>
<body>
<main class="canvas">
  <section class="card card--front">
    <p class="company">528BUILDA</p>
    <div class="divider"></div>
    <div class="contact">
      <p class="contact__name">DANIEL HART</p>
      <p class="contact__role">Managing Director</p>
      <p>Your address, City</p>
      <p>State, Zip 1234</p>
      <p class="contact__item">
        <svg class="contact__icon" viewBox="0 0 12 12"><path fill="#f7941e" d="M2.5 1 L4.5 1 L5 3.5 L3.8 4.3 C4.5 6 6 7.5 7.7 8.2 L8.5 7 L11 7.5 L11 9.5 C11 10.3 10.3 11 9.5 11 C5 11 1 7 1 2.5 C1 1.7 1.7 1 2.5 1Z"/></svg>
        123 456 789
      </p>
      <p class="contact__item">
        <svg class="contact__icon" viewBox="0 0 12 12"><rect x="1" y="2.5" width="10" height="7" fill="#f7941e"/><path d="M1 2.5 L6 6.5 L11 2.5" fill="none" stroke="#181818" stroke-width="1"/></svg>
        info@yourmail.com
      </p>
      <p class="contact__item">
        <svg class="contact__icon" viewBox="0 0 12 12"><circle cx="6" cy="6" r="5" fill="#f7941e"/><path d="M1 6 H11 M6 1 C3.5 3.5 3.5 8.5 6 11 M6 1 C8.5 3.5 8.5 8.5 6 11" fill="none" stroke="#181818" stroke-width="0.8"/></svg>
        www.yourwebsite.com
      </p>
    </div>
  </section>

  <section class="card card--back">
    <p class="company company--back">528BUILDA</p>
  </section>
</main>
</body>
</html>
```